Podiatry clinic requires a modern revamp and editing of existing website.

I would like a fresh new look and updated information for my current business website. An easy to navigate site with prominent address and phone number for call to action. We are a podiatry clinic that focuses on general and sports podiatry.
I would like 4 pages; including Home page, About Us, Services & Contact.
www.brambleridgepodiatry.net

Target Market(s)

Active working professionals.

Industry/Entity Type

Medical

Coding

Coded - Design and coding required

Number of Pages Required

4 page

Font styles to use
Sans Serif

Colors
6b449b

Requirements
Must have
• A modern look with logo and active images; clean and uncluttered. Visible phone number and address for call to action.
• 4 pages - Home, About Us, Services, Contact.
• Home page - update address & service logos.
• About Us - update of personal information.
• Services - Revamp of existing page.
• Contact page to include Google map, email & phone number.
Nice to have
• Ability to add content easily; eg. a blog or adding video onto Home page.
• Link to Facebook page.

```html
<!DOCTYPE html>
<html lang="en">
<head>
<meta charset="utf-8">
<title>Brambleridge Podiatry</title>
<link href="https://fonts.googleapis.com/css2?family=Lato:wght@400;700&family=Poppins:wght@300;500;600&display=swap" rel="stylesheet">
<style>
:root{
  --purple:#4a3797;
  --purple-foot:#5b46a1;
  --purple-btn:#9a86c6;
  --green:#7dc242;
  --orange:#f07421;
  --text:#2b2b2b;
  --muted:#6a6a6a;
  --rule:#cfcfcf;
}
*{margin:0;padding:0;box-sizing:border-box}
html,body{width:892px;height:1200px;overflow:hidden}
body{font-family:"Lato",sans-serif;color:var(--text);position:relative;background:#fff}
.topbar{position:absolute;top:0;left:0;width:892px;height:22px;background:var(--purple);color:#fff;font-size:11px}
.topbar .social{position:absolute;left:427px;top:6px;display:flex;gap:12px}
.topbar .social span{width:10px;height:10px;border-radius:50%;background:#fff;opacity:.85}
.topbar .contact-item{position:absolute;top:0;height:22px;display:flex;align-items:center}
.topbar .icon-box{width:22px;height:22px;background:var(--green);display:flex;align-items:center;justify-content:center;margin-right:8px}
.header{position:absolute;top:22px;left:0;width:892px;height:79px;background:#fff}
.brand{position:absolute;left:76px;top:14px;display:flex;align-items:center;gap:8px;font-family:"Poppins",sans-serif;font-weight:600;font-size:17px;color:var(--purple);line-height:1.1;width:130px}
.brand .dot{width:14px;height:14px;border-radius:50%;background:var(--orange);flex:none}
.nav{position:absolute;top:24px;left:373px;display:flex;align-items:center;font-size:11px;color:var(--purple)}
.nav a{color:var(--purple);text-decoration:none;padding:0 17px;height:31px;line-height:31px}
.nav a.active{border:1px solid var(--purple);font-weight:700;padding:0 17px}
.book{position:absolute;left:670px;top:24px;width:149px;height:31px;background:var(--green);color:#fff;font-family:"Poppins",sans-serif;font-weight:500;font-size:12px;display:flex;align-items:center;justify-content:center;gap:7px}
.hero{position:absolute;top:101px;left:0;width:892px;height:350px;background:linear-gradient(180deg,#cdbfa8 0%,#b59d7b 45%,#8d7656 100%)}
.hero .arrow{position:absolute;top:165px;width:20px;height:20px;border:1px solid #fff;display:flex;align-items:center;justify-content:center}
.hero .caption{position:absolute;left:0;right:0;bottom:14px;text-align:center;color:#fff;font-family:"Poppins",sans-serif;font-weight:600;font-size:22px;text-shadow:0 1px 3px rgba(0,0,0,.4)}
.welcome{position:absolute;top:451px;left:0;width:892px;height:238px}
.welcome h1{position:absolute;left:81px;top:27px;font-family:"Poppins",sans-serif;font-size:26px;font-weight:300;color:var(--orange)}
.welcome h1 b{font-weight:600;color:var(--purple)}
.welcome .rule{position:absolute;left:81px;top:70px;width:479px;height:1px;background:var(--rule)}
.welcome .copy{position:absolute;left:81px;top:81px;width:515px;font-size:10.2px;line-height:16.5px}
.welcome .copy p{margin-bottom:8px}
.welcome .copy strong{font-size:12px}
.welcome .ghost{position:absolute;left:630px;top:70px;font-family:"Poppins",sans-serif;font-weight:600;font-size:28px;line-height:1.2;color:#ddd7ee}
.services{position:absolute;top:689px;left:0;width:892px;height:296px;background:linear-gradient(180deg,#ecebea,#f4f2ee)}
.services h2{position:absolute;left:0;right:0;top:25px;text-align:center;font-family:"Poppins",sans-serif;font-size:25px;font-weight:300;color:var(--orange)}
.services h2 b{font-weight:600;color:var(--purple)}
.services .rule{position:absolute;left:341px;top:68px;width:211px;height:1px;background:var(--rule)}
.card{position:absolute;top:105px;width:362px;height:149px;background:#fff;border:1px solid #ddd;border-radius:4px;overflow:hidden}
.card .photo{position:absolute;left:0;top:0;width:185px;height:149px}
.card .body{position:absolute;left:191px;top:9px;width:165px}
.card h3{font-family:"Poppins",sans-serif;font-weight:600;font-size:17px;color:#111}
.card h4{font-size:10px;font-weight:700;margin:5px 0 6px}
.card p{font-size:10px;line-height:16.5px;color:var(--muted)}
.card .more{display:inline-block;margin-top:9px;background:var(--purple-btn);color:#fff;font-size:10px;font-weight:700;padding:7px 12px}
.footer{position:absolute;top:985px;left:0;width:892px;height:186px;background:var(--purple-foot);color:#fff}
.col{position:absolute;top:28px}
.col h5{font-family:"Poppins",sans-serif;font-weight:500;font-size:12px;padding-bottom:6px;border-bottom:1px solid rgba(255,255,255,.3)}
.col ul{list-style:none;font-size:9px}
.links li{padding:8px 0 8px 10px;border-bottom:1px solid rgba(255,255,255,.15);position:relative}
.links li::before{content:"";position:absolute;left:0;top:11px;border-left:4px solid #fff;border-top:3px solid transparent;border-bottom:3px solid transparent}
.hours li{padding:6px 0;border-bottom:1px solid rgba(255,255,255,.15);line-height:13px}
.hours b{font-weight:700}
.details li{padding:8px 0 12px 14px;position:relative;line-height:13px;border-bottom:1px solid rgba(255,255,255,.15)}
.details svg{position:absolute;left:0;top:10px}
.sep{position:absolute;top:40px;width:1px;height:110px;background:rgba(255,255,255,.15)}
.map{width:169px;height:96px;margin-top:12px;background:linear-gradient(135deg,#e5e0d5,#cfc9bb);border:2px solid #fff}
.copyright{position:absolute;top:1171px;left:0;width:892px;height:29px;background:var(--green);text-align:center;line-height:29px;font-size:10px;color:#333}
</style>
</head>
<body>
<div class="topbar">
  <div class="social"><span></span><span></span><span></span><span></span></div>
  <div class="contact-item" style="left:535px"><div class="icon-box"><svg width="10" height="10" viewBox="0 0 24 24"><path fill="#fff" d="M6.6 10.8a15 15 0 006.6 6.6l2.2-2.2a1 1 0 011-.25 11.4 11.4 0 003.6.57 1 1 0 011 1V20a1 1 0 01-1 1A17 17 0 013 4a1 1 0 011-1h3.5a1 1 0 011 1c0 1.25.2 2.45.57 3.57a1 1 0 01-.25 1z"/></svg></div>555-214-7730</div>
  <div class="contact-item" style="left:647px"><div class="icon-box"><svg width="10" height="8" viewBox="0 0 20 14"><path fill="#fff" d="M0 0h20v14H0z"/><path fill="none" stroke="#7dc242" stroke-width="1.6" d="M0 0l10 8 10-8"/></svg></div>hello@brambleridgepodiatry.net</div>
</div>

<header class="header">
  <div class="brand"><span class="dot"></span>Brambleridge Podiatry</div>
  <nav class="nav">
    <a class="active">Home</a><a>About Us</a><a>Services</a><a>Contact</a>
  </nav>
  <div class="book"><svg width="14" height="14" viewBox="0 0 24 24"><circle cx="10" cy="6" r="4" fill="#fff"/><path fill="#fff" d="M3 22c0-5 3-9 7-9s7 4 7 9z"/></svg>Book Appointment</div>
</header>

<section class="hero" role="img" aria-label="Photo of bare feet walking on a sandy beach at sunset">
  <div class="arrow" style="left:44px"><svg width="10" height="8" viewBox="0 0 10 8"><path d="M9 4H1M4 1L1 4l3 3" stroke="#fff" fill="none" stroke-width="1.4"/></svg></div>
  <div class="arrow" style="left:827px"><svg width="10" height="8" viewBox="0 0 10 8"><path d="M1 4h8M6 1l3 3-3 3" stroke="#fff" fill="none" stroke-width="1.4"/></svg></div>
  <div class="caption">Brambleridge Podiatry is a Podiatry clinic in the heart of Melbourne</div>
</section>

<section class="welcome">
  <h1>Welcome to <b>Brambleridge Podiatry</b></h1>
  <div class="rule"></div>
  <div class="copy">
    <p>Brambleridge Podiatry is a Podiatry clinic in the heart of Melbourne CBD. We are located between Hartley &amp; Vane Streets in the Larkspur Business Centre / Fernlea Hotel Complex. Our podiatrists are fully qualified health professionals who are able to diagnose, treat, manage or help to prevent all medical conditions that affect the feet and lower limb.</p>
    <p>We provide General Podiatry Treatment and some Specialised Services in relation to various foot conditions, including Sports Injuries, Orthotic Therapy and Nail Surgery.</p>
    <p>For Appointments or Enquiries please call us on <strong>1300 555 482</strong> or email: &nbsp;<strong>info@brambleridgepodiatry.net</strong></p>
  </div>
  <div class="ghost">Brambleridge<br>Podiatry</div>
</section>

<section class="services">
  <h2>Our <b>Services</b></h2>
  <div class="rule"></div>
  <article class="card" style="left:73px">
    <div class="photo" role="img" aria-label="Photo of a podiatrist treating a patient's foot" style="background:linear-gradient(135deg,#e9d6c8,#a9c3dc)"></div>
    <div class="body">
      <h3>General Podiatry</h3>
      <h4>Lorem Ipsum is simply dummy tex</h4>
      <p>When an unknown printer took a galley of type and scrambled it to make a type specimen book.</p>
      <span class="more">Read More</span>
    </div>
  </article>
  <article class="card" style="left:457px">
    <div class="photo" role="img" aria-label="Photo of a clinician examining an athlete's leg" style="background:linear-gradient(135deg,#eef0f2,#c9ccd2)"></div>
    <div class="body">
      <h3>Sports Podiatry</h3>
      <h4>Lorem Ipsum is simply dummy tex</h4>
      <p>When an unknown printer took a galley of type and scrambled it to make a type specimen book.</p>
      <span class="more">Read More</span>
    </div>
  </article>
</section>

<footer class="footer">
  <div class="col links" style="left:73px;width:90px">
    <h5>Quick Links</h5>
    <ul><li>Home</li><li>About Us</li><li>Services</li><li>Contact</li></ul>
  </div>
  <div class="sep" style="left:202px"></div>
  <div class="col hours" style="left:241px;width:128px">
    <h5>Hours of Operation</h5>
    <ul>
      <li><b>Monday to Thursday</b><br>10:00 am to 07:00 pm</li>
      <li><b>Friday &amp; Satuday</b><br>10:00 am to 05:00 pm</li>
      <li style="border:none"><b>Sunday</b><br>10:00 am to 01:00 pm</li>
    </ul>
  </div>
  <div class="sep" style="left:408px"></div>
  <div class="col details" style="left:444px;width:138px">
    <h5>Contact Details</h5>
    <ul>
      <li><svg width="7" height="10" viewBox="0 0 14 20"><path fill="#fff" d="M7 0a7 7 0 00-7 7c0 5 7 13 7 13s7-8 7-13a7 7 0 00-7-7zm0 10a3 3 0 110-6 3 3 0 010 6z"/></svg>Suite 208 / 91 Larkspur Lane<br>Melbourne &nbsp;3000</li>
      <li><svg width="8" height="8" viewBox="0 0 24 24"><path fill="#fff" d="M6.6 10.8a15 15 0 006.6 6.6l2.2-2.2a1 1 0 011-.25 11.4 11.4 0 003.6.57 1 1 0 011 1V20a1 1 0 01-1 1A17 17 0 013 4a1 1 0 011-1h3.5a1 1 0 011 1c0 1.25.2 2.45.57 3.57a1 1 0 01-.25 1z"/></svg>1300 555 482</li>
      <li style="border:none"><svg width="8" height="6" viewBox="0 0 20 14"><path fill="#fff" d="M0 0h20v14H0z"/><path fill="none" stroke="#5b46a1" stroke-width="1.6" d="M0 0l10 8 10-8"/></svg>info@brambleridgepodiatry.net</li>
    </ul>
  </div>
  <div class="sep" style="left:616px"></div>
  <div class="col" style="left:650px;width:169px">
    <h5 style="border:none">Location Map</h5>
    <div class="map" role="img" aria-label="Street map showing the clinic location"></div>
  </div>
</footer>

<div class="copyright">Copyright © 2016 &nbsp;<b>Brambleridge Podiatry</b>. All Rights Reserved.</div>
</body>
</html>
```